Need Business Card for our Real Estate Business with Sales Executive's Picture

PANTONE 484 C ( RED)

PANTONE 2766 C ( BLUE

Industry/Entity Type

Real Estate

Contact Information for Business Card

Name, Mobile, email, & picture of Person
Agency Phone, address, Web address

Requirements
Must have
• Our Logo Colours, Agent Picture,

```html
<!DOCTYPE html>
<html lang="en">
<head>
<meta charset="utf-8">
<title>Meridian Real Estate – Business Card</title>
<link href="https://fonts.googleapis.com/css2?family=Tinos:wght@400;700&display=swap" rel="stylesheet">
<style>
  :root {
    --navy: #13246a;
    --navy-deep: #0a1646;
    --red: #8c1022;
    --red-deep: #6e0a19;
    --white: #ffffff;
    --ink: #1a2a66;
    --stage: #e9e6e1;
    --photo-light: #3c5bb0;
    --photo-dark: #14296a;
  }
  * { box-sizing: border-box; margin: 0; padding: 0; }
  html, body { width: 1200px; height: 780px; overflow: hidden; }
  body {
    background: var(--stage);
    font-family: "Tinos", "Times New Roman", serif;
    display: flex; align-items: center; justify-content: center; gap: 60px;
  }
  .card {
    position: relative; width: 525px; height: 300px; overflow: hidden;
    background: radial-gradient(ellipse at 60% 40%, var(--navy) 0%, var(--navy-deep) 100%);
    box-shadow: 0 8px 24px rgba(0, 0, 0, .25);
  }
  .web-band {
    position: absolute; left: 0; right: 0; bottom: 0; height: 42px;
    background: linear-gradient(90deg, var(--red), var(--red-deep));
    color: var(--white); font-size: 14px; letter-spacing: 3px;
    display: flex; align-items: center; justify-content: flex-end; padding-right: 34px;
  }
  .info-band {
    position: absolute; left: 0; right: 0; bottom: 42px; height: 96px;
    background: var(--white);
  }
  .agent-photo {
    position: absolute; left: 20px; bottom: 0; width: 200px; height: 190px;
    background: linear-gradient(160deg, var(--photo-light) 0%, var(--photo-dark) 100%);
  }
  .contact {
    position: absolute; left: 236px; bottom: 52px; right: 16px; color: var(--ink);
  }
  .contact .name { font-size: 19px; letter-spacing: 1px; text-transform: uppercase; }
  .contact .role { font-size: 13px; color: var(--red); margin-bottom: 8px; }
  .contact .line { font-size: 11.5px; line-height: 1.5; white-space: nowrap; }
  .contact .label { color: var(--red); font-weight: 700; }
  .wordmark {
    position: absolute; color: var(--white);
    font-size: 30px; font-weight: 400; white-space: nowrap;
  }
  .card-front .wordmark { right: 28px; top: 58px; }
  .card-back .wordmark { left: 50%; top: 42%; transform: translate(-50%, -50%); font-size: 36px; }
</style>
</head>
<body>
  <section class="card card-front">
    <div class="info-band"></div>
    <div class="web-band">www.meridianhomes.com</div>
    <p class="wordmark">Meridian Real Estate</p>
    <div class="agent-photo" role="img" aria-label="Portrait of the sales executive in a blue suit"></div>
    <div class="contact">
      <p class="name">Daniel Hart</p>
      <p class="role">Owner</p>
      <p class="line"><span class="label">M:</span> (555) 014-2368 | <span class="label">E:</span> hello@meridianhomes.com</p>
      <p class="line"><span class="label">A:</span> PO Box 48, Harbour Lane, Melbourne</p>
    </div>
  </section>

  <section class="card card-back">
    <div class="web-band">www.meridianhomes.com</div>
    <p class="wordmark">Meridian Real Estate</p>
  </section>
</body>
</html>
```